Brand Identity & Marketing Website Design for Professional Football Scouting Software

Merivantalo is a professional football scouting report generation software.
It is a standalone desktop application that allows football clubs, agencies and players to generate structured, executive-level A4 PDF scouting reports.
This is NOT:
a betting platform
a fan website
a football news blog
a SaaS subscription platform
This is a premium document-generation software tool designed for professional use inside football organizations.
The brand must reflect:
• Structure
• Authority
• Precision
• Professionalism
• Trust
• Executive-level quality
Think consulting firm, performance analysis tool, structured business software.
Not flashy sports media.
What We Need
We are looking for:
1️⃣ Logo Design
2️⃣ Full Brand Identity System
3️⃣ Marketing Website UI/UX Design
(Development is NOT included in this job.)
Important Product Context
Merivantalo is sold as a one-time purchase software package.
After purchase: • Customers download the software
• Install it locally
• Generate reports offline
There is no recurring subscription.
There is no SaaS login platform.
The website is a marketing and purchase website only.
1️⃣ Logo Design
The logo must:
• Be professional and timeless
• Work in both light and dark backgrounds
• Be scalable (website header, app icon, favicon)
• Avoid cliché football logo styles (no shields, mascots, flashy emblems)
• Feel modern, clean, and strong
We prefer:
• Clean typography-based logo
• Minimal symbol integration
• Strong visual balance
• Suitable for software branding
Name:
Merivantalo
Optional tagline:
The leading platform for professional football scouting reports
Deliver:
• Full logo
• Icon-only version (for desktop app icon)
• Light & dark variations
2️⃣ Brand Identity System
We need a structured design system that supports:
• Marketing website
• Desktop application UI
• PDF report previews
Please define:
• Primary color palette
• Secondary color palette
• Accent colors
• Typography system (professional, highly readable)
• Heading hierarchy
• UI styling guidelines
• Light mode & dark mode principles
The design must feel:
• Minimal
• Grid-based
• Clean
• Premium
• Corporate
Avoid:
• Neon colors
• Heavy gradients
• Overly sporty visuals
• Gaming aesthetics
3️⃣ Marketing Website Design (UI/UX Only)
We need full website design in Figma for:
• Homepage
• Product Overview
• Packages Page (Club / Agency / Player)
• How It Works
• Demo Section
• FAQ
• Contact
• Purchase / Download Page
Design must include:
• Hero section
• Feature explanation sections
• Structured benefits
• Product screenshots placement
• Pricing comparison layout
• Clear call-to-action areas
• Professional footer
Responsive design required (Desktop-first, mobile adaptation).
Important:
Content copy will be provided by us.
Designer focuses on layout, structure, hierarchy and visual design.
Target Audience
• Professional football clubs
• Scouting departments
• Player agencies
• Semi-professional and professional players
This is primarily B2B, with some B2C.
Style Direction
We are looking for:
• Strong typography
• Balanced whitespace
• Structured layouts
• Subtle but confident use of color
• Professional photography (if used)
• Premium software feel
The website and brand must feel trustworthy and high-level.
Deliverables
• Logo files (AI, SVG, PNG)
• Brand guideline document (PDF)
• Figma file with full website UI
• Icon assets (app icon, favicon)
• Color and typography system

Need extra days to review

```html
<!DOCTYPE html>
<html lang="en">
<head>
<meta charset="utf-8">
<title>Merivantalo — Professional Football Scouting Reports</title>
<link rel="stylesheet" href="https://fonts.googleapis.com/css2?family=Archivo:wght@600;700;800;900&family=Poppins:wght@400;500;600;700&display=swap">
<style>
:root{
  --navy:#13307a;
  --navy-deep:#0b1d4d;
  --ink:#0a1433;
  --black:#0b0b0d;
  --charcoal:#17181c;
  --white:#ffffff;
  --text:#1b2233;
  --muted:#6b7285;
  --line:#e3e6ee;
  --green:#3fbf4f;
  --red:#d93030;
  --head:"Archivo",Arial,sans-serif;
  --body:"Poppins",Helvetica,sans-serif;
}
*{box-sizing:border-box;margin:0;padding:0}
html,body{width:1200px;height:5112px;overflow:hidden;background:var(--white)}
body{font-family:var(--body);color:var(--text);position:relative}
section,header,footer{position:absolute;left:0;width:1200px}
.abs{position:absolute}
.btn{display:inline-flex;align-items:center;justify-content:center;font-family:var(--body);font-weight:600;font-size:14px;border-radius:6px;height:44px;padding:0 26px;text-decoration:none}
.btn-navy{background:var(--navy);color:var(--white)}
.btn-dark{background:var(--ink);color:var(--white)}
.btn-light{background:var(--white);color:var(--navy)}
.section-title{font-family:var(--head);font-weight:800;font-size:44px;letter-spacing:.5px;text-transform:uppercase;text-align:center;width:100%;left:0}
.section-sub{left:270px;width:660px;text-align:center;font-size:15px;line-height:1.6;color:var(--muted)}

/* Header */
.site-header{top:0;height:120px;background:var(--white)}
.brand{left:112px;top:36px;display:flex;align-items:center;gap:12px}
.brand-square{width:46px;height:46px;background:var(--navy);border-radius:6px}
.brand-name{font-family:var(--head);font-weight:800;font-size:27px;color:var(--navy-deep);letter-spacing:.5px;line-height:1}
.brand-tag{font-size:10px;color:var(--muted);margin-top:4px}
.header-actions{right:112px;top:22px;display:flex;gap:14px}
.header-actions .btn{height:40px;font-size:13px}
.main-nav{right:112px;top:78px;display:flex;gap:44px;font-size:14px;font-weight:500;color:var(--text)}
.main-nav .active{color:var(--navy);border-bottom:2px solid var(--navy);padding-bottom:3px}

/* Hero */
.hero{top:120px;height:720px;overflow:hidden}
.hero-media{inset:0;background:linear-gradient(100deg,#07112e 0%,#0d2357 45%,#1f4f9e 75%,#0c1f4c 100%);clip-path:polygon(0 0,100% 0,100% 82%,0 96%)}
.hero-stripe{inset:0;background:var(--navy);clip-path:polygon(0 96%,100% 82%,100% 86%,0 100%)}
.hero-copy{left:112px;top:100px;color:var(--white);width:560px}
.hero-title{font-family:var(--head);font-weight:900;font-size:74px;line-height:1;letter-spacing:1px}
.hero-title-sub{font-family:var(--head);font-weight:800;font-size:44px;line-height:1.1;margin-top:8px}
.hero-tagline{font-family:var(--head);font-weight:800;font-size:25px;margin-top:34px;letter-spacing:.5px}
.hero-desc{font-size:16px;line-height:1.6;margin-top:22px;width:420px;color:#dfe6f5}
.hero-actions{display:flex;gap:18px;margin-top:34px}

/* Who it's for */
.audience{top:840px;height:720px}
.audience .section-title{top:110px}
.audience .section-sub{top:178px}
.audience-card{top:260px;width:320px;height:330px;background:var(--white);border-radius:16px;box-shadow:0 8px 28px rgba(11,29,77,.12);padding:10px;text-align:center}
.audience-card.is-active{box-shadow:0 10px 34px rgba(11,29,77,.25);outline:2px solid #c9d2e6}
.card-media{height:210px;border-radius:12px}
.card-title{font-family:var(--head);font-weight:800;font-size:16px;margin-top:16px;letter-spacing:.4px}
.card-text{font-size:12px;color:var(--muted);line-height:1.5;margin:8px auto 0;width:230px}
.card-link{font-size:12px;font-weight:600;color:var(--navy);text-decoration:underline;margin-top:8px;display:inline-block}
.audience .cta{top:630px;left:0;width:100%;display:flex;justify-content:center}

/* Who we are */
.about{top:1560px;height:580px}
.about-photo{left:120px;top:50px;width:390px;height:390px;border-radius:50%;background:radial-gradient(circle at 40% 40%,#e8edf5,#9fb2cf 60%,#2a4682);box-shadow:-20px 20px 0 var(--navy-deep),0 14px 40px rgba(0,0,0,.2)}
.about-copy{left:640px;top:100px;width:450px}
.about-title{font-family:var(--head);font-weight:800;font-size:44px;text-transform:uppercase}
.about-text{font-size:14px;line-height:1.7;color:var(--muted);margin-top:22px}

/* Benefits */
.benefits{top:2140px;height:780px}
.benefits-bg{inset:0;background:linear-gradient(180deg,#0c1f52 0%,#163a8c 50%,#0e2660 100%);clip-path:polygon(0 14%,50% 0,100% 14%,100% 92%,0 100%)}
.benefits .section-title{top:220px;color:var(--white)}
.benefits .section-sub{top:286px;color:#d2dbef}
.benefit-card{top:356px;width:228px;height:310px;background:var(--white);border-radius:14px;text-align:center;padding:28px 18px}
.benefit-icon{width:64px;height:64px;border-radius:50%;background:var(--navy-deep);margin:0 auto;display:flex;align-items:center;justify-content:center}
.benefit-title{font-family:var(--head);font-weight:800;font-size:15px;margin-top:22px;line-height:1.3;text-transform:uppercase}
.benefit-text{font-size:12.5px;color:var(--muted);line-height:1.6;margin-top:12px}

/* Comparison */
.compare{top:2920px;height:800px}
.compare .section-title{top:90px}
.compare .section-sub{top:156px}
.compare-table{left:172px;top:228px;width:856px;height:500px;border-radius:18px;overflow:hidden;box-shadow:0 12px 36px rgba(11,29,77,.16);display:grid;grid-template-columns:320px 168px 180px 188px;background:var(--white)}
.col{display:flex;flex-direction:column}
.col-head{height:62px;display:flex;align-items:center;font-family:var(--head);font-weight:800;font-size:14px;letter-spacing:.5px}
.col-features .col-head{padding-left:40px;border-bottom:1px solid var(--line)}
.col-club{background:var(--navy)}
.col-agency{background:var(--charcoal)}
.col-player{background:var(--black)}
.col-club .col-head,.col-agency .col-head,.col-player .col-head{justify-content:center;color:var(--white);border-bottom:1px solid rgba(255,255,255,.15)}
.cell{height:46px;display:flex;align-items:center;font-size:13px}
.col-features .cell{padding-left:40px}
.col-club .cell,.col-agency .cell,.col-player .cell{justify-content:center}
.dot{width:11px;height:11px;border-radius:50%;background:var(--green)}
.dot.no{background:var(--red)}

/* FAQ */
.faq{top:3720px;height:880px}
.faq .section-title{top:60px}
.faq-item{left:220px;width:800px;border:1px solid #d6dbe6;border-radius:10px;background:var(--white);padding:0 26px}
.faq-item.is-open{box-shadow:0 8px 26px rgba(11,29,77,.14);border-color:#b9c3da}
.faq-q{height:68px;display:flex;align-items:center;justify-content:space-between;font-family:var(--head);font-weight:800;font-size:14px;color:var(--navy-deep);letter-spacing:.3px}
.faq-a{font-size:13.5px;line-height:1.6;color:var(--muted)}
.faq-a strong{display:block;color:var(--text);font-weight:500;margin-bottom:14px}
.faq .cta{top:790px;left:0;width:100%;display:flex;justify-content:center}

/* Footer */
.site-footer{top:4600px;height:512px}
.footer-bg{inset:0;background:linear-gradient(180deg,#0a1a46,#060f2b);clip-path:polygon(0 10%,100% 0,100% 100%,0 100%)}
.footer-edge{inset:0;background:var(--navy);clip-path:polygon(0 6%,100% 0,100% 4%,0 10%)}
.footer-brand{left:112px;top:170px;width:340px;color:var(--white)}
.footer-brand .brand-name{color:var(--white);font-size:30px}
.footer-brand .brand-square{background:var(--white)}
.footer-about{font-size:14px;line-height:1.6;margin-top:22px;color:#d6deef}
.footer-col{top:170px;color:var(--white)}
.footer-col h4{font-family:var(--head);font-weight:800;font-size:22px;text-transform:uppercase;letter-spacing:.5px}
.footer-col ul{list-style:disc;padding-left:18px;margin-top:22px}
.footer-col li{font-size:13.5px;line-height:2;color:#d6deef}
.footer-bar{left:0;top:440px;width:1200px;height:72px;border-top:1px solid rgba(255,255,255,.18);display:flex;align-items:center;justify-content:center;color:#c8d1e6;font-size:13px}
</style>
</head>
<body>

<header class="site-header">
  <div class="abs brand">
    <span class="brand-square"></span>
    <div>
      <div class="brand-name">MERIVANTALO</div>
      <div class="brand-tag">Platform for Professional Football Scouting Reports</div>
    </div>
  </div>
  <div class="abs header-actions">
    <a class="btn btn-dark" href="#">Purchase Software</a>
    <a class="btn btn-navy" href="#">Contact Us</a>
  </div>
  <nav class="abs main-nav">
    <span class="active">HOME</span><span>Products</span><span>Packages</span><span>How It Works</span><span>Demo</span><span>FAQ</span>
  </nav>
</header>

<section class="hero">
  <div class="abs hero-media" role="img" aria-label="Analyst reviewing football performance data on desktop screens"></div>
  <div class="abs hero-stripe"></div>
  <div class="abs hero-copy">
    <h1 class="hero-title">PROFESSIONAL</h1>
    <div class="hero-title-sub">FOOTBALL SCOUTING<br>REPORTS.</div>
    <div class="hero-tagline">STRUCTURED. EXECUTIVE. PRECISE.</div>
    <p class="hero-desc">Standalone desktop software for generating executive level A4 scouting reports.</p>
    <div class="hero-actions">
      <a class="btn btn-navy" href="#">Purchase Software</a>
      <a class="btn btn-light" href="#">View Sample Report</a>
    </div>
  </div>
</section>

<section class="audience">
  <h2 class="abs section-title">Who It's For</h2>
  <p class="abs section-sub">Sed ut perspiciatis unde omnis iste natus error sit voluptatem accusantium doloremque laudantium, totam rem aperiam, eaque ipsa quae</p>
  <article class="abs audience-card" style="left:112px">
    <div class="card-media" role="img" aria-label="Phone showing a football scouting app on a pitch" style="background:linear-gradient(160deg,#2f6b3a,#123a22 60%,#0a1a12)"></div>
    <h3 class="card-title">FOOTBALL CLUBS</h3>
    <p class="card-text">Sed ut perspiciatis unde omnis iste natus error sit voluptatem dolore</p>
    <a class="card-link" href="#">Explore Details</a>
  </article>
  <article class="abs audience-card is-active" style="left:440px">
    <div class="card-media" role="img" aria-label="Agency analysis room with match footage screens" style="background:linear-gradient(160deg,#1e4a8a,#0e2550 55%,#2c6b3d)"></div>
    <h3 class="card-title">PLAYER AGENCIES</h3>
    <p class="card-text">Sed ut perspiciatis unde omnis iste natus error sit voluptatem dolore</p>
    <a class="card-link" href="#">Explore Details</a>
  </article>
  <article class="abs audience-card" style="left:768px">
    <div class="card-media" role="img" aria-label="Football on the pitch in a floodlit stadium" style="background:linear-gradient(170deg,#2a5fb0,#0f2a63 55%,#1f5a2c)"></div>
    <h3 class="card-title">FOOTBALL PLAYERS</h3>
    <p class="card-text">Sed ut perspiciatis unde omnis iste natus error sit voluptatem dolore</p>
    <a class="card-link" href="#">Explore Details</a>
  </article>
  <div class="abs cta"><a class="btn btn-navy" href="#">Explore More Details</a></div>
</section>

<section class="about">
  <div class="abs about-photo" role="img" aria-label="Hands working on a laptop with data charts"></div>
  <div class="abs about-copy">
    <h2 class="about-title">Who We Are</h2>
    <p class="about-text">Sed ut perspiciatis unde omnis iste natus error sit voluptatem accusantium doloremque laudantium, totam rem aperiam, eaque ipsa quae ab illo inventore veritatis et quasi architecto beatae vitae dicta sunt explicabo. Nemo enim ipsam voluptatem quia voluptas sit aspernatur aut odit aut fugit.</p>
    <p class="about-text">Neque porro quisquam est, qui dolorem ipsum quia dolor sit amet, consectetur adipisci velit, sed quia non numquam eius modi tempora incidunt ut labore.</p>
    <a class="btn btn-navy" href="#" style="margin-top:30px">Learn More</a>
  </div>
</section>

<section class="benefits">
  <div class="abs benefits-bg" role="img" aria-label="Stadium under floodlights in deep blue tones"></div>
  <h2 class="abs section-title">Structured Benefits</h2>
  <p class="abs section-sub">Sed ut perspiciatis unde omnis iste natus error sit voluptatem accusantium doloremque laudantium, totam rem aperiam, eaque ipsa quae</p>
  <article class="abs benefit-card" style="left:108px">
    <div class="benefit-icon"><svg width="30" height="30" viewBox="0 0 24 24" fill="none" stroke="#fff" stroke-width="1.6"><rect x="5" y="3" width="14" height="18" rx="1.5"/><path d="M8 8h8M8 12h8M8 16h5"/></svg></div>
    <h3 class="benefit-title">Structured Report Architecture</h3>
    <p class="benefit-text">Pre-defined sections for technical, tactical and psychological evaluation.</p>
  </article>
  <article class="abs benefit-card" style="left:360px">
    <div class="benefit-icon"><svg width="30" height="30" viewBox="0 0 24 24" fill="none" stroke="#fff" stroke-width="1.6"><path d="M6 3h9l4 4v14H6z"/><path d="M15 3v4h4M9 13h6M9 17h6"/></svg></div>
    <h3 class="benefit-title">Executive-Ready PDF Generation</h3>
    <p class="benefit-text">Generate clean A4 PDFs formatted for boardroom, recruitment.</p>
  </article>
  <article class="abs benefit-card" style="left:612px">
    <div class="benefit-icon"><svg width="30" height="30" viewBox="0 0 24 24" fill="none" stroke="#fff" stroke-width="1.6"><rect x="3" y="4" width="18" height="12" rx="1.5"/><path d="M9 20h6M12 16v4"/></svg></div>
    <h3 class="benefit-title">Offline Desktop Application</h3>
    <p class="benefit-text">Operate locally. No browser logins. No cloud dependency.</p>
  </article>
  <article class="abs benefit-card" style="left:864px">
    <div class="benefit-icon"><svg width="30" height="30" viewBox="0 0 24 24" fill="none" stroke="#fff" stroke-width="1.6"><circle cx="12" cy="12" r="8"/><path d="M8 12l3 3 5-6"/></svg></div>
    <h3 class="benefit-title">Consistent Evaluation Standards</h3>
    <p class="benefit-text">Maintain internal alignment across scouting departments.</p>
  </article>
</section>

<section class="compare">
  <h2 class="abs section-title">Why It's Different</h2>
  <p class="abs section-sub">Sed ut perspiciatis unde omnis iste natus error sit voluptatem accusantium doloremque laudantium, totam rem aperiam, eaque ipsa quae</p>
  <div class="abs compare-table">
    <div class="col col-features">
      <div class="col-head">FEATURES</div>
      <div class="cell" style="margin-top:8px">Desktop Application</div>
      <div class="cell">Offline Operation</div>
      <div class="cell">Structured Report Framework</div>
      <div class="cell">A4 Executive PDF Export</div>
      <div class="cell">Unlimited Report Generation</div>
      <div class="cell">Department Standardization</div>
      <div class="cell">Priority Support</div>
      <div class="cell">Remote Onboarding Session</div>
      <div class="cell">Upgrade Option Available</div>
    </div>
    <div class="col col-club">
      <div class="col-head">CLUB</div>
      <div class="cell" style="margin-top:8px"><span class="dot"></span></div>
      <div class="cell"><span class="dot"></span></div><div class="cell"><span class="dot"></span></div>
      <div class="cell"><span class="dot"></span></div><div class="cell"><span class="dot"></span></div>
      <div class="cell"><span class="dot"></span></div><div class="cell"><span class="dot"></span></div>
      <div class="cell"><span class="dot"></span></div><div class="cell"><span class="dot"></span></div>
    </div>
    <div class="col col-agency">
      <div class="col-head">AGENCY</div>
      <div class="cell" style="margin-top:8px"><span class="dot"></span></div>
      <div class="cell"><span class="dot"></span></div><div class="cell"><span class="dot"></span></div>
      <div class="cell"><span class="dot"></span></div><div class="cell"><span class="dot"></span></div>
      <div class="cell"><span class="dot"></span></div><div class="cell"><span class="dot no"></span></div>
      <div class="cell"><span class="dot"></span></div><div class="cell"><span class="dot"></span></div>
    </div>
    <div class="col col-player">
      <div class="col-head">PLAYER</div>
      <div class="cell" style="margin-top:8px"><span class="dot"></span></div>
      <div class="cell"><span class="dot"></span></div><div class="cell"><span class="dot"></span></div>
      <div class="cell"><span class="dot"></span></div><div class="cell"><span class="dot"></span></div>
      <div class="cell"><span class="dot no"></span></div><div class="cell"><span class="dot no"></span></div>
      <div class="cell"><span class="dot no"></span></div><div class="cell"><span class="dot"></span></div>
    </div>
  </div>
</section>

<section class="faq">
  <h2 class="abs section-title">Frequently Asked Questions</h2>
  <div class="abs faq-item is-open" style="top:140px;height:170px">
    <div class="faq-q">IS MERIVANTALO A SAAS PLATFORM?<svg width="14" height="14" viewBox="0 0 14 14"><path d="M2 9l5-5 5 5" fill="none" stroke="#0b1d4d" stroke-width="2"/></svg></div>
    <div class="faq-a"><strong>No. It is a downloadable desktop application.</strong>Sed ut perspiciatis unde omnis iste natus error sit voluptatem accusantium doloremque laudantium, totam rem aperiam, eaque ipsa quae ab illo inventore veritatis et quasi architecto beatae vitae dicta.</div>
  </div>
  <div class="abs faq-item" style="top:340px"><div class="faq-q">DOES IT REQUIRE INTERNET ACCESS?<svg width="14" height="14" viewBox="0 0 14 14"><path d="M2 5l5 5 5-5" fill="none" stroke="#0b1d4d" stroke-width="2"/></svg></div></div>
  <div class="abs faq-item" style="top:442px"><div class="faq-q">IS THERE A RECURRING SUBSCRIPTION?<svg width="14" height="14" viewBox="0 0 14 14"><path d="M2 5l5 5 5-5" fill="none" stroke="#0b1d4d" stroke-width="2"/></svg></div></div>
  <div class="abs faq-item" style="top:544px"><div class="faq-q">UT ENIM AD MINIMA VENIAM, QUIS NOSTRUM EXERCITATIONEM ULLAM CORPORIS?<svg width="14" height="14" viewBox="0 0 14 14"><path d="M2 5l5 5 5-5" fill="none" stroke="#0b1d4d" stroke-width="2"/></svg></div></div>
  <div class="abs faq-item" style="top:646px"><div class="faq-q">SED UT PERSPICIATIS UNDE OMNIS ISTE NATUS ERROR SIT VOLUPTATEM?<svg width="14" height="14" viewBox="0 0 14 14"><path d="M2 5l5 5 5-5" fill="none" stroke="#0b1d4d" stroke-width="2"/></svg></div></div>
  <div class="abs cta"><a class="btn btn-navy" href="#">Learn More</a></div>
</section>

<footer class="site-footer">
  <div class="abs footer-bg"></div>
  <div class="abs footer-edge"></div>
  <div class="abs footer-brand">
    <div style="display:flex;align-items:center;gap:12px"><span class="brand-square"></span><span class="brand-name">MERIVANTALO</span></div>
    <p class="footer-about">The software is designed to reflect institutional standards, not casual reporting.</p>
  </div>
  <div class="abs footer-col" style="left:520px">
    <h4>Quick Links</h4>
    <ul><li>Home</li><li>Product Overview</li><li>How It Works</li><li>Contact Us</li><li>Purchase Here</li></ul>
  </div>
  <div class="abs footer-col" style="left:745px">
    <h4>Other Links</h4>
    <ul><li>Packages</li><li>Demo</li><li>FAQ</li><li>Contact Us</li><li>Purchase Here</li></ul>
  </div>
  <div class="abs footer-col" style="left:960px">
    <h4>Follow Us</h4>
    <ul><li>Kickfeed</li><li>Snapline</li><li>Workboard</li><li>Clipstream</li></ul>
  </div>
  <div class="abs footer-bar">(C) Copyright 2026 | All Rights Reserved</div>
</footer>

</body>
</html>
```